Quick Straightforward Billboard Redesign

- Design billboard sized for 10 foot' x 36' foot width live area size and please include bleeds 6" around all sides
- Exact blue color match is imperative in headline, logo, phone number bubble or wherever used. C-83 / M-45 / Y-1 / K-0-
- What I hope to illustrate is that our company offers the best porch screening in the area area, in regards to quality, expertise, durability, storms proof, but we do not build screen porches.
- Current board is attached below from previous designer, and as you can see sizing was off, white space on edges make it appear to be sized incorrectly.
- I also attached my own little mock up idea well well if it helps, favorite image, logo, headline, etc and ideas perhaps on expanding or making this better?

Thanks so much!

Target Market(s)

Drivers and passengers, Southeastern NC, are of immense new construction and high end homes.

Industry/Entity Type

Construction

Colors
0054AA
0677BA
7BADD7
CADEEF
E8F1F8

Requirements
Must have
• Blue color matching
Nice to have
• Design spins or other thoughts on my little mock up

```html
<!DOCTYPE html>
<html lang="en">
<head>
<meta charset="utf-8">
<title>Harborline Screens Billboard</title>
<link href="https://fonts.googleapis.com/css2?family=Anton&family=Oswald:wght@600&family=Montserrat:wght@800&display=swap" rel="stylesheet">
<style>
  :root {
    --brand-blue: #0054AA;
    --band-blue: #0A5CA8;
    --accent-blue: #0677BA;
    --sky-light: #7BADD7;
    --mist: #CADEEF;
    --panel-white: #F4F6F8;
    --panel-grey: #E6E9EC;
    --brand-green: #00A651;
    --white: #FFFFFF;
    --page: #E9EDF1;
  }
  html, body {
    margin: 0;
    width: 1200px;
    height: 1091px;
    overflow: hidden;
    background: var(--page);
  }
  .stage {
    width: 1200px;
    height: 1091px;
    display: flex;
    align-items: center;
    justify-content: center;
  }
  .billboard {
    width: 1140px;
    height: auto;
    display: block;
    box-shadow: 0 6px 24px rgba(0, 0, 0, 0.15);
  }
  .brand-name {
    font-family: "Oswald", "Arial Narrow", sans-serif;
    font-weight: 600;
    font-size: 78px;
    fill: var(--brand-blue);
  }
  .headline {
    font-family: "Anton", "Impact", sans-serif;
    font-size: 112px;
  }
  .headline--blue { fill: var(--brand-blue); }
  .headline--green { fill: var(--brand-green); }
  .phone-number {
    font-family: "Montserrat", "Arial", sans-serif;
    font-weight: 800;
    font-size: 84px;
    fill: var(--white);
  }
</style>
</head>
<body>
<main class="stage">
  <svg class="billboard" viewBox="0 0 1835 530" xmlns="http://www.w3.org/2000/svg" aria-label="Harborline Screens billboard">
    <defs>
      <linearGradient id="panelShade" x1="0" y1="0" x2="1" y2="1">
        <stop offset="0" stop-color="var(--panel-grey)"/>
        <stop offset="1" stop-color="var(--panel-white)"/>
      </linearGradient>
      <linearGradient id="porchTones" x1="0" y1="0" x2="0" y2="1">
        <stop offset="0" stop-color="#EEF1F3"/>
        <stop offset="0.2" stop-color="#DCE3E8"/>
        <stop offset="0.3" stop-color="#7BADD7"/>
        <stop offset="0.45" stop-color="#8FA86A"/>
        <stop offset="0.6" stop-color="#A7A08E"/>
        <stop offset="1" stop-color="#D9D2C4"/>
      </linearGradient>
    </defs>

    <!-- Text panel -->
    <polygon class="text-panel" points="0,0 928,0 1125,530 0,530" fill="url(#panelShade)"/>

    <!-- Porch photograph area -->
    <polygon class="porch-photo" role="img" aria-label="Photo of a screened coastal porch with wicker seating overlooking a lake" points="960,0 1835,0 1835,530 1155,530" fill="url(#porchTones)"/>

    <!-- Diagonal divider stripe -->
    <polygon class="divider-stripe" points="928,0 962,0 1157,530 1123,530" fill="var(--accent-blue)"/>

    <!-- Brand -->
    <rect class="brand-square" x="130" y="74" width="62" height="62" fill="var(--accent-blue)"/>
    <text class="brand-name" x="212" y="137" textLength="590" lengthAdjust="spacingAndGlyphs">HARBORLINE SCREENS</text>

    <!-- Headline -->
    <text class="headline headline--blue" x="64" y="268" textLength="820" lengthAdjust="spacingAndGlyphs">SCREEN YOUR PORCH.</text>
    <text class="headline headline--green" x="64" y="375" textLength="832" lengthAdjust="spacingAndGlyphs">BUILT FOR THE COAST.</text>

    <!-- Contact band -->
    <polygon class="contact-band" points="0,410 838,420 880,530 0,530" fill="var(--band-blue)"/>
    <polygon class="contact-accent" points="845,420 888,420 928,530 885,530" fill="var(--brand-green)"/>

    <g class="phone-icon">
      <circle cx="110" cy="466" r="34" fill="var(--brand-green)"/>
      <path d="M97 446c3-2 6-1 7 2l4 8c1 2 0 4-2 5l-3 2c2 5 6 9 11 11l2-3c1-2 3-3 5-2l8 4c3 1 4 4 2 7l-3 4c-2 2-5 3-8 2-14-5-24-15-29-29-1-3 0-6 2-8z" fill="var(--white)"/>
    </g>
    <text class="phone-number" x="170" y="496" textLength="565" lengthAdjust="spacingAndGlyphs">555.014.2287</text>
  </svg>
</main>
</body>
</html>
```